I would like a single page website for Skyward Rentals Pacific. In the file list provided there is basic information to be included as well as our logo with colors, fonts and images to be included.
Site must be very simple and be able to be loaded onto smart phones etc very quickly.
Site needs to be very smart in appearance

Target Market(s)

All prospective drone customers from Police to Parties.

Industry/Entity Type

Hire

Requirements
Must have
• Must have variation of color schemes supplied
Nice to have
• Must be very eye catching without going over the top
Should not have
• Anything slow to load.

```html
<!DOCTYPE html>
<html lang="en">
<head>
<meta charset="utf-8">
<title>Skyward Rentals Pacific</title>
<link rel="stylesheet" href="https://fonts.googleapis.com/css2?family=Barlow:wght@400;500;600;700&display=swap">
<style>
:root{
  --navy:#34477a;
  --navy-deep:#1d2a6b;
  --header:#3b4b7c;
  --ink:#333;
  --muted:#555;
  --services-bg:#f7f3f3;
  --about-bg:#efeded;
  --contact-bg:#f3f3f3;
  --footer-bg:#1f1e1f;
  --rule:#d4d4d4;
  --white:#fff;
}
*{margin:0;padding:0;box-sizing:border-box}
html,body{width:729px;height:1200px;overflow:hidden;background:var(--white)}
body{font-family:"Barlow",Arial,sans-serif;color:var(--ink);position:relative}
.abs{position:absolute}

/* header */
.site-header{position:absolute;left:0;top:0;width:729px;height:50px;background:var(--header)}
.brand-box{position:absolute;left:60px;top:0;width:130px;height:65px;background:var(--white);display:flex;align-items:center;justify-content:center;gap:5px;z-index:3}
.brand-mark{width:8px;height:8px;background:var(--navy-deep)}
.brand-name{font-weight:700;font-size:12px;line-height:13px;color:var(--navy-deep);letter-spacing:.5px;text-transform:uppercase}
.main-nav{position:absolute;left:227px;top:23px;display:flex;font-size:7.5px;font-weight:500;color:var(--white);text-transform:uppercase}
.main-nav span{margin-right:0}
.main-nav .active{color:#1a2a8c}
.search-box{position:absolute;left:572px;top:21px;width:97px;height:15px;background:#a9a9aa}
.search-box svg{position:absolute;right:4px;top:3px}

/* hero */
.hero{position:absolute;left:0;top:50px;width:729px;height:327px;background:linear-gradient(180deg,#3d5a86 0%,#4b6486 35%,#5d5548 70%,#2c2a2c 100%)}
.hero-kicker{position:absolute;left:60px;top:123px;font-size:16px;font-weight:500;color:var(--white);letter-spacing:.5px}
.hero-title{position:absolute;left:60px;top:144px;font-size:22px;font-weight:700;color:var(--white);letter-spacing:.5px}
.hero-arrow{position:absolute;top:186px;width:18px;height:18px;border-radius:50%;background:rgba(90,90,90,.85)}
.hero-arrow svg{position:absolute;left:4px;top:4px}

/* welcome */
.section-title{position:absolute;left:0;width:729px;text-align:center;font-size:16px;font-weight:500;color:var(--navy);letter-spacing:.5px}
.welcome-text{position:absolute;left:86px;top:433px;width:557px;text-align:center;font-size:7.2px;line-height:12.5px;color:var(--muted)}
.welcome-rule{position:absolute;left:286px;top:487px;width:156px;height:1px;background:var(--rule)}

/* services */
.services{position:absolute;left:0;top:518px;width:729px;height:287px;background:var(--services-bg)}
.service-photo{position:absolute;top:58px;width:175px;height:94px;border:1px solid #cfcfd8}
.service-name{position:absolute;top:165px;width:175px;text-align:center;font-size:13px;font-weight:500;color:#111}
.service-text{position:absolute;top:185px;width:185px;text-align:center;font-size:7px;line-height:12.5px;color:var(--muted)}
.btn{position:absolute;background:var(--navy);color:var(--white);font-weight:600;display:flex;align-items:center;justify-content:center}
.btn-small{top:231px;width:70px;height:20px;font-size:7.5px}

/* about */
.about{position:absolute;left:0;top:805px;width:729px;height:201px;background:var(--about-bg)}
.about-title{position:absolute;left:78px;top:16px;font-size:16px;font-weight:500;color:var(--navy)}
.about-list{position:absolute;left:78px;top:44px;list-style:none;font-size:7.2px;color:#444}
.about-list li{height:15.5px;display:flex;align-items:center}
.about-list li::before{content:"";width:4px;height:4px;border:1.2px solid #555;border-radius:50%;margin-right:7px}
.btn-videos{left:78px;top:117px;width:124px;height:31px;font-size:9.5px}
.video{position:absolute;left:374px;top:20px;width:286px;height:147px;border:1px solid #ccc;background:var(--white)}
.video-frame{position:absolute;left:0;top:0;width:284px;height:128px;background:linear-gradient(180deg,#3a3a3a 0%,#6b6560 60%,#8a8784 100%)}
.video-bar{position:absolute;left:0;top:128px;width:284px;height:17px}

/* contact */
.contact{position:absolute;left:0;top:1006px;width:729px;height:116px;background:var(--contact-bg)}
.divider{position:absolute;top:14px;width:1px;height:76px;background:var(--rule)}
.contact-head{position:absolute;top:26px;display:flex;align-items:center;gap:7px;font-size:12.5px;font-weight:500;color:#222}
.contact-lines{position:absolute;top:52px;font-size:7.5px;line-height:14px;font-weight:500;color:#333}
.social{position:absolute;left:419px;top:29px;font-size:7px;color:#333}
.social li{list-style:none;display:flex;align-items:center;height:21.5px}
.social li::before{content:"";width:9px;height:9px;background:var(--navy-deep);margin-right:9px}

/* footer */
.site-footer{position:absolute;left:0;top:1122px;width:729px;height:78px;background:var(--footer-bg)}
.footer-brand{position:absolute;left:78px;top:16px;display:flex;align-items:center;gap:5px}
.footer-brand .brand-mark{background:#4a5a8a}
.footer-brand .brand-name{color:#4a5a8a;font-size:14px;line-height:15px}
.copyright{position:absolute;left:220px;top:38px;font-size:7.5px;font-weight:600;color:var(--white)}
</style>
</head>
<body>

<header class="site-header">
  <div class="brand-box">
    <span class="brand-mark"></span>
    <span class="brand-name">Skyward Rentals<br>Pacific</span>
  </div>
  <nav class="main-nav">
    <span class="active" style="position:absolute;left:0">Home</span>
    <span style="position:absolute;left:63px;white-space:nowrap">About Us</span>
    <span style="position:absolute;left:141px">Services</span>
    <span style="position:absolute;left:218px">FAQs</span>
    <span style="position:absolute;left:278px">Contacts</span>
  </nav>
  <div class="search-box">
    <svg width="8" height="8" viewBox="0 0 8 8"><circle cx="3.2" cy="3.2" r="2.3" fill="none" stroke="#fff" stroke-width="1.2"/><line x1="5" y1="5" x2="7.4" y2="7.4" stroke="#fff" stroke-width="1.4"/></svg>
  </div>
</header>

<section class="hero" role="img" aria-label="Photo of a white camera drone flying between tall glass office towers against a blue sky">
  <div class="hero-kicker">AEROSAFE CERTIFIED COMPANY</div>
  <div class="hero-title">FULL AEROSAFE COMPLIANCE STANDARDS</div>
  <div class="hero-arrow" style="left:19px"><svg width="10" height="10" viewBox="0 0 10 10"><path d="M6.5 1.5 3 5l3.5 3.5" fill="none" stroke="#2a2a2a" stroke-width="2"/></svg></div>
  <div class="hero-arrow" style="left:685px"><svg width="10" height="10" viewBox="0 0 10 10"><path d="M3.5 1.5 7 5 3.5 8.5" fill="none" stroke="#2a2a2a" stroke-width="2"/></svg></div>
</section>

<h2 class="section-title" style="top:398px">WELCOME TO OUR WEBSITE</h2>
<p class="welcome-text">Ipsum generators on the Internet tend to repeat predefined chunks as necessary, making this the first true generator on the Internet. It uses a dictionary of over 200 Latin words, combined with a handful of model sentence structures, to generate Lorem Ipsum which looks reasonable. The generated Lorem Ipsum is therefore always free from repetition, injected humour, or non-characteristic words etc.</p>
<div class="welcome-rule"></div>

<section class="services">
  <h2 class="section-title" style="top:15px">OUR SERVICES</h2>

  <div class="service-photo" style="left:70px;background:linear-gradient(135deg,#c9b4ae 0%,#d9a79a 50%,#8a7c8e 100%)" role="img" aria-label="Photo of a family celebrating a birthday party"></div>
  <div class="service-name" style="left:65px">Parties</div>
  <p class="service-text" style="left:60px">Lorem ipsum dolor sit amet, consectetur adipiscing elit. Etiam aliquet, ipsum eget sodales blandit, neque purus lacinia nulla, quis sagittis elit</p>
  <div class="btn btn-small" style="left:118px">Read More »</div>

  <div class="service-photo" style="left:275px;background:linear-gradient(160deg,#6d8fd6 0%,#8fa9e0 55%,#5a6b8c 100%)" role="img" aria-label="Photo of a security camera against a blue sky"></div>
  <div class="service-name" style="left:270px">Surveillance</div>
  <p class="service-text" style="left:265px">Lorem ipsum dolor sit amet, consectetur adipiscing elit. Etiam aliquet, ipsum eget sodales blandit, neque purus lacinia nulla, quis sagittis elit</p>
  <div class="btn btn-small" style="left:322px">Read More »</div>

  <div class="service-photo" style="left:479px;background:linear-gradient(135deg,#3a3a3a 0%,#8a8a8a 45%,#b59c34 100%)" role="img" aria-label="Photo of a chained padlock on a laptop keyboard"></div>
  <div class="service-name" style="left:474px">Security</div>
  <p class="service-text" style="left:469px">Lorem ipsum dolor sit amet, consectetur adipiscing elit. Etiam aliquet, ipsum eget sodales blandit, neque purus lacinia nulla, quis sagittis elit</p>
  <div class="btn btn-small" style="left:526px">Read More »</div>
</section>

<section class="about">
  <h2 class="about-title">About Us</h2>
  <ul class="about-list">
    <li>Special Occasions, Childrens Birthday Parties, Weddings</li>
    <li>Sporting events</li>
    <li>Real Estate Brochures</li>
    <li>Construction project updates for remote stake holders</li>
  </ul>
  <div class="btn btn-videos">VIEW ALL VIDEOS »</div>
  <div class="video">
    <div class="video-frame" role="img" aria-label="Video still of runners racing along a road">
      <svg class="abs" style="left:132px;top:55px" width="20" height="20" viewBox="0 0 20 20"><circle cx="10" cy="10" r="8.5" fill="none" stroke="rgba(255,255,255,.7)" stroke-width="1.5"/><path d="M8 6v8l6-4z" fill="rgba(255,255,255,.7)"/></svg>
    </div>
    <svg class="video-bar" viewBox="0 0 284 17">
      <circle cx="11" cy="8.5" r="4.5" fill="none" stroke="#333" stroke-width="1.2"/><path d="M10 6.5v4l3-2z" fill="#333"/>
      <rect x="20" y="7.5" width="231" height="2" fill="#555"/><rect x="20" y="7.5" width="4" height="2" fill="#c0282d"/>
      <path d="M256 6.5h2l3-2.5v9l-3-2.5h-2z" fill="#333"/><path d="M263 6q1.5 2.5 0 5" fill="none" stroke="#333"/>
      <path d="M273 4l3 3M279 4l-3 3M273 13l3-3M279 13l-3-3" stroke="#333" stroke-width="1.3"/>
    </svg>
  </div>
</section>

<section class="contact">
  <div class="contact-head" style="left:78px">
    <svg width="15" height="15" viewBox="0 0 15 15"><rect width="15" height="15" rx="3" fill="var(--navy-deep)"/><path d="M4.5 3.5l1.8 2.2-1 1.2q1 2 3 3l1.2-1 2.2 1.8-1.2 1.6q-4.5-.5-7-6z" fill="#fff"/></svg>
    Telephone
  </div>
  <div class="contact-lines" style="left:78px">0491 570 156<br>0491 570 156</div>
  <div class="divider" style="left:197px"></div>

  <div class="contact-head" style="left:244px">
    <svg width="19" height="14" viewBox="0 0 19 14"><rect width="19" height="14" rx="1.5" fill="var(--navy-deep)"/><path d="M1.5 2l8 6 8-6" fill="none" stroke="#fff" stroke-width="1.3"/></svg>
    Email Us
  </div>
  <div class="contact-lines" style="left:244px">hello@skywardrentals.example<br>bookings@skywardrentals.example</div>
  <div class="divider" style="left:370px"></div>

  <ul class="social">
    <li>Journal</li>
    <li>Community</li>
    <li>Videos</li>
  </ul>
  <div class="divider" style="left:507px"></div>

  <div class="contact-head" style="left:551px">
    <svg width="11" height="16" viewBox="0 0 11 16"><path d="M5.5 0A5.5 5.5 0 0 0 0 5.5C0 9.5 5.5 16 5.5 16S11 9.5 11 5.5A5.5 5.5 0 0 0 5.5 0z" fill="var(--navy-deep)"/><circle cx="5.5" cy="5.5" r="2" fill="#fff"/></svg>
    Address
  </div>
  <div class="contact-lines" style="left:551px">Lorem Ipsum dollor<br>Ipsum generator amet</div>
</section>

<footer class="site-footer">
  <div class="footer-brand">
    <span class="brand-mark"></span>
    <span class="brand-name">SKYWARD RENTALS<br>PACIFIC</span>
  </div>
  <div class="copyright">© 2015 Privacy Policy</div>
</footer>

</body>
</html>
```